job report

Designer – Professional Plumbing Job Report Template

Overview

We are seeking a skilled designer to create a professional, easy-to-use Job Report template for a commercial and maintenance plumbing business.
The report will be used for clients, property managers, facilities managers, strata, and retail centres and must clearly communicate findings, works completed, and recommendations in a polished, compliant, and branded format.

The final document must be suitable for PDF delivery, email, and ongoing reuse.

Objectives

Present plumbing works in a clear, professional, and defensible report format

Improve client understanding of findings and recommendations

Provide a repeatable template that can be used across maintenance, reactive, and investigative works

Allow easy insertion of text, tables, and photos

Report Structure (Minimum Inclusions)
1. Cover Page

Company logo and branding

Report title (e.g. Plumbing Job Report / Investigation Report)

Client name

Site address

Job reference / work order number

Date of attendance

Technician / contractor name

2. Client & Site Details

Client / company name

Site address

Contact person

Contact details

Access notes (after-hours, tenant access, etc.)

3. Reason for Attendance

Clear description of why attendance was required

Call-out type (reactive, scheduled maintenance, investigation, emergency, etc.)

Reported issue or scope requested by client

4. Findings / Observations

Detailed findings discovered on site

Condition of pipework, fixtures, drainage, or systems

Any contributing factors identified

Notes on compliance, wear, damage, or risk

(This section should support bullet points and paragraphs.)

5. Works Carried Out

Step-by-step description of works completed

Equipment used (e.g. jetter, CCTV camera, leak detection, flex shaft, etc.)

Repairs, replacements, testing, and verification

Confirmation that systems were tested and operational on completion

6. Photos & Visual Evidence

Clearly labelled photo sections

Before / during / after photos

Space for photo captions and explanations

Logical layout that aligns photos with written findings

7. Recommendations

Clearly separated from works completed

Urgent vs non-urgent recommendations

Preventative maintenance advice

Upgrade or replacement suggestions

Risk-based language where appropriate

8. Limitations & Exclusions

Areas not inspected

Access limitations

Assumptions made during inspection

Items outside scope of works

9. Conclusion

Summary of outcome

Confirmation of current system status

Next steps (if any)

10. Sign-Off

Contractor / technician name

Company name

Date

Optional client acknowledgement section

Design Requirements

Clean, professional layout

Commercial / trade-appropriate styling (not overly creative)

Easy-to-read fonts

Consistent headings and spacing

Logical flow for busy property managers

Editable format (Word / Google Docs / InDesign source file)

Final export-ready PDF version

Bonus (Nice to Have)

Traffic-light system (Green / Amber / Red) for condition reporting

Iconography for findings, repairs, and recommendations

Optional sections for compliance notes (AS/NCC references)

Space for QR codes or job reference numbers

Deliverables

Editable master report template

PDF version

Instructions or notes for ongoing use

```html
<!DOCTYPE html>
<html lang="en">
<head>
<meta charset="utf-8">
<title>Flowline Plumbing – Job Report Template</title>
<link href="https://fonts.googleapis.com/css2?family=Inter:wght@400;500;600;800&display=swap" rel="stylesheet">
<style>
  :root {
    --canvas: #c6c6c6;
    --paper: #ffffff;
    --brand-blue: #2fbde2;
    --band-edge: #e8f7fc;
    --band-mid: #3cc3e7;
    --ink: #1d1d1f;
    --label: #2a2a2a;
    --field: #f4f4f4;
    --field-line: #dcdcdc;
    --footer: #1d2022;
    --footer-num: #131517;
    --footer-text: #f2f2f2;
  }
  * { box-sizing: border-box; margin: 0; padding: 0; }
  html, body { width: 1200px; height: 527px; overflow: hidden; }
  body {
    background: var(--canvas);
    font-family: "Inter", Arial, sans-serif;
    color: var(--ink);
    position: relative;
  }
  .page {
    position: absolute;
    top: 31px;
    width: 364px;
    height: 471px;
    background: var(--paper);
    box-shadow: 0 3px 10px rgba(0,0,0,0.18);
  }
  .page--cover { left: 33px; }
  .page--client { left: 422px; }
  .page--reason { left: 810px; }

  .brand {
    position: absolute;
    top: 33px;
    left: 0; right: 0;
    text-align: center;
    font-weight: 800;
    font-size: 20px;
    letter-spacing: 0.3px;
    color: var(--brand-blue);
  }

  .title-band {
    position: absolute;
    top: 93px;
    left: 0; right: 0;
    height: 34px;
    background: linear-gradient(90deg, var(--band-edge) 0%, var(--band-mid) 30%, var(--band-mid) 70%, var(--band-edge) 100%);
    display: flex;
    align-items: center;
    justify-content: center;
  }
  .title-band h1 {
    font-weight: 800;
    font-size: 18px;
    letter-spacing: -0.2px;
    color: #fff;
    text-shadow: 0 1px 2px rgba(0,0,0,0.25);
  }

  .section-heading {
    position: absolute;
    left: 33px;
    font-weight: 600;
    font-size: 7.4px;
    line-height: 9px;
  }
  .field {
    position: absolute;
    left: 33px;
    width: 297px;
  }
  .field label {
    display: block;
    font-size: 5.8px;
    line-height: 8px;
    color: var(--label);
    margin-bottom: 3.5px;
  }
  .field .box {
    height: 22.4px;
    background: var(--field);
    border: 0.5px solid var(--field-line);
  }
  .field--half { width: 143.5px; }
  .field--half.right { left: 187px; }
  .field--third { width: 94px; }
  .field--third.mid { left: 134.5px; }
  .field--third.end { left: 236px; }
  .field--heading label {
    font-weight: 600;
    font-size: 7.4px;
    line-height: 9px;
    color: var(--ink);
    margin-bottom: 5px;
  }
  .field .box--issue { height: 46px; }

  .callout-types {
    position: absolute;
    top: 157px;
    left: 33px;
    list-style: none;
    width: 297px;
    height: 9px;
  }
  .callout-types li {
    position: absolute;
    display: flex;
    align-items: center;
    font-size: 7.2px;
    color: var(--label);
  }
  .callout-types .check {
    width: 5px; height: 5px;
    border: 0.5px solid #9a9a9a;
    border-radius: 1px;
    margin-right: 6px;
  }

  .report-sections {
    position: absolute;
    top: 250px;
    left: 33px;
    width: 297px;
    display: grid;
    grid-template-columns: 1fr 1fr;
    column-gap: 10px;
    row-gap: 6px;
  }
  .report-section h3 {
    font-weight: 600;
    font-size: 6.2px;
    line-height: 8px;
    margin-bottom: 3px;
    color: var(--ink);
  }
  .report-section .box {
    height: 30px;
    background: var(--field);
    border: 0.5px solid var(--field-line);
  }
  .report-section--wide { grid-column: 1 / -1; }
  .report-section--wide .box { height: 24px; }

  .footer {
    position: absolute;
    left: 0; right: 0; bottom: 0;
    height: 31px;
    background: var(--footer);
    display: flex;
  }
  .footer p {
    flex: 1;
    padding: 0 20px 0 13px;
    align-self: center;
    font-size: 4.5px;
    line-height: 7px;
    color: var(--footer-text);
  }
  .footer .page-num {
    width: 34px;
    background: var(--footer-num);
    color: #fff;
    font-weight: 600;
    font-size: 6.5px;
    display: flex;
    align-items: center;
    justify-content: center;
  }
</style>
</head>
<body>

<section class="page page--cover">
  <div class="brand">Flowline Plumbing</div>
  <div class="title-band"><h1>PLUMBING JOB REPORT</h1></div>
  <h2 class="section-heading" style="top:139px">Client</h2>
  <div class="field field--half" style="top:155px"><label>First name</label><div class="box"></div></div>
  <div class="field field--half right" style="top:155px"><label>Last name</label><div class="box"></div></div>
  <div class="field" style="top:198px"><label>Site address</label><div class="box"></div></div>
  <div class="field" style="top:244px"><label>Job reference / work order number</label><div class="box"></div></div>
  <div class="field" style="top:288px"><label>Date of attendance</label><div class="box"></div></div>
  <div class="field" style="top:334px"><label>Technician / contractor name</label><div class="box"></div></div>
  <footer class="footer">
    <p>Lorem ipsum dolor sit amet, consectetur adipiscing elit, sed do eiusmod tempor incididunt ut labore et dolore magna aliqua. Ut enim ad minim veniam, quis nostrud exercitation ullamco laboris nisi ut aliquip ex ea commodo consequat.</p>
    <div class="page-num">1</div>
  </footer>
</section>

<section class="page page--client">
  <div class="brand">Flowline Plumbing</div>
  <div class="title-band"><h1>CLIENT &amp; SITE DETAILS</h1></div>
  <h2 class="section-heading" style="top:139px">Client / company name</h2>
  <div class="field field--half" style="top:155px"><label>First name</label><div class="box"></div></div>
  <div class="field field--half right" style="top:155px"><label>Last name</label><div class="box"></div></div>
  <div class="field" style="top:198px"><label>Site address</label><div class="box"></div></div>
  <div class="field" style="top:244px"><label>Contact Person</label><div class="box"></div></div>
  <h2 class="section-heading" style="top:288px">Contact Details</h2>
  <div class="field field--third" style="top:305px"><label>Address</label><div class="box"></div></div>
  <div class="field field--third mid" style="top:305px"><label>Email</label><div class="box"></div></div>
  <div class="field field--third end" style="top:305px"><label>Phone</label><div class="box"></div></div>
  <div class="field" style="top:351px"><label>Access Notes</label><div class="box"></div></div>
  <footer class="footer">
    <p>Lorem ipsum dolor sit amet, consectetur adipiscing elit, sed do eiusmod tempor incididunt ut labore et dolore magna aliqua. Ut enim ad minim veniam, quis nostrud exercitation ullamco laboris nisi ut aliquip ex ea commodo consequat.</p>
    <div class="page-num">2</div>
  </footer>
</section>

<section class="page page--reason">
  <div class="brand">Flowline Plumbing</div>
  <div class="title-band"><h1>REASON FOR ATTENDANCE</h1></div>
  <h2 class="section-heading" style="top:139px">Call-out type</h2>
  <ul class="callout-types">
    <li style="left:0"><span class="check"></span>Reactive</li>
    <li style="left:59.5px"><span class="check"></span>Scheduled Maintenance</li>
    <li style="left:172.5px"><span class="check"></span>Investigation</li>
    <li style="left:250.5px"><span class="check"></span>Emergency</li>
  </ul>
  <div class="field field--heading" style="top:184px"><label>Reported Issue / Scope Requested</label><div class="box box--issue"></div></div>
  <div class="report-sections">
    <div class="report-section"><h3>4. Findings / Observations</h3><div class="box"></div></div>
    <div class="report-section"><h3>5. Works Carried Out</h3><div class="box"></div></div>
    <div class="report-section"><h3>6. Photos &amp; Visual Evidence</h3><div class="box"></div></div>
    <div class="report-section"><h3>7. Recommendations</h3><div class="box"></div></div>
    <div class="report-section"><h3>8. Limitations &amp; Exclusions</h3><div class="box"></div></div>
    <div class="report-section"><h3>9. Conclusion</h3><div class="box"></div></div>
    <div class="report-section report-section--wide"><h3>10. Sign-Off</h3><div class="box"></div></div>
  </div>
  <footer class="footer">
    <p>Lorem ipsum dolor sit amet, consectetur adipiscing elit, sed do eiusmod tempor incididunt ut labore et dolore magna aliqua. Ut enim ad minim veniam, quis nostrud exercitation ullamco laboris nisi ut aliquip ex ea commodo consequat.</p>
    <div class="page-num">3</div>
  </footer>
</section>

</body>
</html>
```